Business Card Design

We need a new business card design for a company based in Alderbrook, CO. We provide business consulting services in the information technology / services space. We like variations of the color blue, aqua, black, light tan, and white. Would like "cool" tones. The design should clearly communicate professionalism. Think outside the box - we don't want something "typical". Our company name is "Halvery Consulting, LLC".
Updates

Thank you all for your submissions. We have seen some very creative and inspired designs. We have made a decision and will be moving forward with that design. Appreciate all of the hard work.

Industry/Entity Type

Information Technology

Contact Information for Business Card

Megan Halvery Strube
218 West Birchfold Ridge Dr.
Alderbrook, CO 76418

```html
<!DOCTYPE html>
<html lang="en">
<head>
<meta charset="utf-8">
<title>Halvery Consulting, LLC — Business Card</title>
<link rel="stylesheet" href="https://fonts.googleapis.com/css2?family=Open+Sans:wght@300;400;700&display=swap">
<style>
  :root {
    --backdrop: #e9e7e4;
    --card-white: #ffffff;
    --card-black: #0c0b0b;
    --ink: #141414;
    --ink-soft: #444444;
    --rule: #8a8a8a;
    --reverse-ink: #f2f2f2;
  }
  * { box-sizing: border-box; margin: 0; padding: 0; }
  html, body {
    width: 1200px;
    height: 892px;
    overflow: hidden;
    background: var(--backdrop);
    font-family: "Open Sans", Arial, sans-serif;
  }
  .canvas {
    width: 1200px;
    height: 892px;
    display: flex;
    align-items: center;
    justify-content: center;
    gap: 50px;
  }
  .card {
    width: 520px;
    height: 297px;
    position: relative;
    box-shadow: 0 8px 22px rgba(0,0,0,0.18);
  }
  .card--front { background: var(--card-white); color: var(--ink); }
  .card--back { background: var(--card-black); color: var(--reverse-ink); display: flex; align-items: center; justify-content: center; }

  .brand {
    display: flex;
    align-items: center;
    gap: 10px;
    font-weight: 300;
    text-transform: uppercase;
    letter-spacing: 0.08em;
    line-height: 1.25;
  }
  .brand__square { border: 1px solid currentColor; flex: none; }
  .card--front .brand { position: absolute; left: 44px; top: 124px; font-size: 10px; }
  .card--front .brand__square { width: 16px; height: 16px; }
  .card--back .brand { font-size: 17px; gap: 14px; }
  .card--back .brand__square { width: 26px; height: 26px; }

  .identity { position: absolute; left: 258px; top: 92px; }
  .identity__name { font-size: 18px; font-weight: 700; letter-spacing: 0.01em; }
  .identity__title { font-size: 10px; color: var(--ink-soft); margin-top: 2px; }

  .contact { position: absolute; left: 244px; top: 158px; list-style: none; font-size: 9.5px; color: var(--ink-soft); }
  .contact__item { display: flex; align-items: center; height: 19px; white-space: nowrap; }
  .contact__label { width: 20px; font-size: 11px; color: var(--ink); }
  .contact__bar { width: 1px; height: 10px; background: var(--rule); margin-right: 9px; }
</style>
</head>
<body>
<main class="canvas">
  <section class="card card--front" aria-label="Business card front">
    <div class="brand">
      <span class="brand__square"></span>
      <span class="brand__name">Halvery<br>Consulting, LLC</span>
    </div>
    <div class="identity">
      <h1 class="identity__name">Megan Halvery Strube</h1>
      <p class="identity__title">CEO, Consultant</p>
    </div>
    <ul class="contact">
      <li class="contact__item"><span class="contact__label">m</span><span class="contact__bar"></span>555-826-0148</li>
      <li class="contact__item"><span class="contact__label">e</span><span class="contact__bar"></span>megan.strube@halverymail.com</li>
      <li class="contact__item"><span class="contact__label">a</span><span class="contact__bar"></span>218 West Birchfold Ridge Dr. Alderbrook, CO 76418</li>
    </ul>
  </section>

  <section class="card card--back" aria-label="Business card back">
    <div class="brand">
      <span class="brand__square"></span>
      <span class="brand__name">Halvery<br>Consulting, LLC</span>
    </div>
  </section>
</main>
</body>
</html>
```